Realtor branding business card

modern, simple and self branding. Broker office logo needs to be used but not emphasized. Looking to brand myself

Target Market(s)

buyers, sellers and investors

Industry/Entity Type

Realtor

Contact Information for Business Card

Sample of my current business card on file

Requirements
Must have
• my website - tobiasmerrowkl.com
• Realtor logo
• Fair housing logo
Nice to have
• Colors from office logo but not a must
Should not have
• Do not want headshot

```html
<!DOCTYPE html>
<html lang="en">
<head>
<meta charset="utf-8">
<title>Tobias Merrow, PA – Business Card</title>
<link href="https://fonts.googleapis.com/css2?family=Roboto:wght@400;500;700&display=swap" rel="stylesheet">
<style>
  :root {
    --navy: #2a1670;
    --red: #d9261c;
    --ink: #4a4a4a;
    --paper: #ffffff;
    --backdrop: #e4e4e4;
  }
  * { box-sizing: border-box; margin: 0; padding: 0; }
  html, body {
    width: 1125px; height: 1200px; overflow: hidden;
    background: var(--backdrop);
    font-family: "Roboto", Arial, sans-serif;
  }
  .card {
    position: absolute; left: 166px; width: 800px; height: 455px;
    overflow: hidden;
  }
  .card-front { top: 103px; background: var(--paper); }
  .card-back { top: 620px; background: var(--navy); }

  .brand {
    position: absolute; right: 38px; text-align: right;
    font-weight: 700;
  }
  .card-front .brand { top: 92px; color: var(--navy); }
  .brand-name { display: block; font-size: 52px; line-height: 56px; letter-spacing: -1px; }
  .brand-sub { display: block; font-size: 26px; line-height: 30px; margin-top: 2px; }

  .name-marker {
    position: absolute; left: 0; top: 263px; width: 15px; height: 46px;
    background: var(--red);
  }
  .agent-name {
    position: absolute; left: 38px; top: 257px;
    font-size: 29px; font-weight: 700; color: var(--navy);
  }
  .agent-title {
    position: absolute; left: 40px; top: 292px;
    font-size: 19px; font-weight: 500; color: var(--red);
  }
  .title-rule {
    position: absolute; left: 111px; right: 38px; top: 304px;
    height: 2px; background: var(--red);
  }
  .contact-list {
    position: absolute; left: 40px; top: 330px; list-style: none;
    font-size: 19px; color: var(--ink); line-height: 25px;
  }
  .contact-list li { display: flex; align-items: center; gap: 11px; }
  .contact-list svg { width: 17px; height: 17px; fill: var(--navy); flex: none; }
  .office-address {
    position: absolute; right: 38px; top: 330px; text-align: right;
    font-size: 19px; color: var(--ink); line-height: 25px; font-style: normal;
  }
  .footer-band {
    position: absolute; left: 0; right: 0; bottom: 0; height: 12px;
    background: var(--navy);
  }

  .card-back .brand { top: 52px; right: 40px; color: #fff; }
  .card-back .brand-name { font-size: 64px; line-height: 68px; }
  .card-back .brand-sub { font-size: 32px; line-height: 34px; margin-top: 0; }
  .back-url {
    position: absolute; right: 40px; top: 158px;
    font-size: 19px; line-height: 24px; letter-spacing: 7px; margin-right: -7px;
    color: #fff;
  }
  .badges {
    position: absolute; right: 42px; bottom: 34px; display: flex; gap: 6px; align-items: flex-end;
  }
  .badge { background: #fff; }
  .badge-member { width: 36px; height: 40px; }
  .badge-housing { width: 60px; height: 40px; }
</style>
</head>
<body>
  <section class="card card-front">
    <div class="brand">
      <span class="brand-name">Hearth Line</span>
      <span class="brand-sub">Realty Group</span>
    </div>

    <span class="name-marker"></span>
    <h1 class="agent-name">Tobias Merrow, PA</h1>
    <p class="agent-title">Realtor</p>
    <span class="title-rule"></span>

    <ul class="contact-list">
      <li>
        <svg viewBox="0 0 24 24" aria-hidden="true"><path d="M6.6 10.8a15.2 15.2 0 0 0 6.6 6.6l2.2-2.2a1 1 0 0 1 1-.25 11.4 11.4 0 0 0 3.6.57 1 1 0 0 1 1 1V20a1 1 0 0 1-1 1A17 17 0 0 1 3 4a1 1 0 0 1 1-1h3.5a1 1 0 0 1 1 1c0 1.25.2 2.45.57 3.57a1 1 0 0 1-.25 1z"/></svg>
        407.555.0142
      </li>
      <li>
        <svg viewBox="0 0 24 24" aria-hidden="true"><path d="M7 1h10a2 2 0 0 1 2 2v18a2 2 0 0 1-2 2H7a2 2 0 0 1-2-2V3a2 2 0 0 1 2-2zm0 3v14h10V4zm5 15.5a1 1 0 1 0 0 2 1 1 0 0 0 0-2z"/></svg>
        407.555.0187
      </li>
      <li>
        <svg viewBox="0 0 24 24" aria-hidden="true"><path d="M2 5h20v14H2zm2 2v.5l8 5 8-5V7zm0 2.8V17h16V9.8l-8 5z"/></svg>
        Merrowrealty@mailbox.com
      </li>
    </ul>

    <address class="office-address">
      482 North Laurelwood Dr.<br>
      Cedar Hollow, FL 32790<br>
      www.tobiasmerrowkl.com
    </address>

    <span class="footer-band"></span>
  </section>

  <section class="card card-back">
    <div class="brand">
      <span class="brand-name">Hearth Line</span>
      <span class="brand-sub">Realty Group</span>
    </div>
    <p class="back-url">www.tobiasmerrowkl.com</p>
    <div class="badges">
      <span class="badge badge-member" role="img" aria-label="Realtor membership badge"></span>
      <span class="badge badge-housing" role="img" aria-label="Equal housing opportunity badge"></span>
    </div>
  </section>
</body>
</html>
```